Thornvale Agribusiness Consulting needs a Website Design.

We need a website design for a new company based in UK. Thornvale offers agribusiness consulting and farm design services to farmers, smallholders and the wider agribusiness industry to assist clients in adopting more sustainable and regenerative production, processing and marketing practices.
Services are offered face-to-face and on a remote platform.
Services are offered in the UK and overseas.
We would like to see designs that reflect the natural environment, business and sustainability. Desired colours; green, blue, grey. The final design should communicate professionalism in the rural economy.
The design should be able to be customized by the client to make future changes and additions.
Target Market(s)
Farmers, smallholders, and the agricultural industry in UK and overseas.
Industry/Entity Type
Agribusiness
Number of Pages Required
4 page
Look and feel
Each slider illustrates characteristics of the customer's brand and the style your logo design should communicate.

```html
<!DOCTYPE html>
<html lang="en">
<head>
<meta charset="utf-8">
<title>Thornvale Agribusiness Consulting</title>
<link rel="stylesheet" href="https://fonts.googleapis.com/css2?family=Roboto:wght@400;500;700&family=Open+Sans:wght@400;600&family=Great+Vibes&display=swap">
<style>
  :root {
    --ink: #2b2b2b;
    --text: #555555;
    --muted: #8a8a8a;
    --line: #e6e6e6;
    --teal: #0fa39a;
    --blue: #1a8fd0;
    --green: #8cc63f;
    --dark: #3c3c3c;
    --field: #e8e8e8;
    --white: #ffffff;
  }
  * { box-sizing: border-box; margin: 0; padding: 0; }
  html, body { width: 930px; height: 1200px; overflow: hidden; background: var(--white); }
  body { position: relative; font-family: "Open Sans", Arial, sans-serif; color: var(--text); }
  a { color: inherit; text-decoration: none; }

  /* Header */
  .site-header { position: absolute; left: 0; top: 0; width: 930px; height: 96px; }
  .brand { position: absolute; left: 64px; top: 40px; display: flex; align-items: center; gap: 8px;
    font-family: "Roboto", Arial, sans-serif; font-weight: 700; font-size: 18px; color: var(--ink); letter-spacing: .5px; }
  .brand-dot { width: 14px; height: 14px; border-radius: 50%; background: var(--green); }
  .top-contact { position: absolute; right: 58px; top: 13px; display: flex; gap: 20px; font-size: 11px; color: var(--ink); }
  .top-contact span { display: flex; align-items: center; gap: 5px; }
  .main-nav { position: absolute; right: 106px; top: 55px; display: flex; gap: 30px;
    font-family: "Roboto", Arial, sans-serif; font-weight: 500; font-size: 12px; color: var(--ink); }
  .main-nav .active { color: var(--teal); }
  .search-btn { position: absolute; left: 848px; top: 50px; width: 24px; height: 24px; border-radius: 50%;
    background: var(--blue); display: flex; align-items: center; justify-content: center; }

  /* Hero */
  .hero { position: absolute; left: 0; top: 96px; width: 930px; height: 414px;
    background: linear-gradient(180deg, #9ea4a8 0%, #c3c7ca 35%, #6b7479 72%, #5c8a3a 85%, #6e9c3e 100%); }
  .hero-arrow { position: absolute; top: 194px; width: 27px; height: 27px; background: #5a5a5a;
    display: flex; align-items: center; justify-content: center; }
  .hero-arrow.prev { left: 0; }
  .hero-arrow.next { right: 0; }

  /* Service cards */
  .services { position: absolute; left: 47px; top: 475px; width: 836px; height: 276px; background: var(--white); padding: 11px 10px 0; }
  .service-row { display: flex; border: 1px solid var(--line); border-top: 0; height: 265px; }
  .service { width: 272px; border-right: 1px solid var(--line); overflow: hidden; }
  .service:last-child { border-right: 0; }
  .service-photo { height: 157px; }
  .photo-cattle { background: linear-gradient(180deg, #4e7d3a 0%, #3f6e2c 40%, #7fb536 70%, #9cc93c 100%); }
  .photo-eggs { background: linear-gradient(135deg, #f2f2f2 0%, #d9d9d9 50%, #eeeeee 100%); }
  .photo-produce { background: linear-gradient(135deg, #6b8f3a 0%, #c0603a 45%, #d8b070 75%, #5f7a3a 100%); }
  .service-body { padding: 18px 8px 0 20px; }
  .service-title { font-family: "Roboto", Arial, sans-serif; font-weight: 500; font-size: 15px; color: var(--ink); }
  .service-rule { width: 28px; height: 2px; margin: 8px 0 10px; }
  .rule-teal { background: var(--teal); }
  .rule-blue { background: var(--blue); }
  .rule-green { background: var(--green); }
  .service-text { font-size: 10.8px; line-height: 17px; letter-spacing: -0.1px; color: var(--text); white-space: nowrap; }

  /* Welcome */
  .welcome-heading { position: absolute; left: 57px; top: 776px; width: 186px; text-align: right; }
  .welcome-script { display: block; font-family: "Great Vibes", cursive; font-size: 25px; color: var(--ink); line-height: 26px; }
  .welcome-name { display: block; text-align: left; font-family: "Roboto", Arial, sans-serif; font-weight: 700; font-size: 30px; color: var(--dark); letter-spacing: .5px; line-height: 34px; }
  .welcome-copy { position: absolute; left: 300px; top: 779px; width: 580px; font-size: 10.5px; line-height: 20px; letter-spacing: -0.05px; color: var(--text); white-space: nowrap; }
  .learn-more { position: absolute; left: 300px; top: 895px; width: 80px; height: 22px; border-radius: 11px;
    background: var(--dark); color: var(--white); font-family: "Roboto", Arial, sans-serif; font-size: 10px;
    display: flex; align-items: center; justify-content: center; }

  .divider { position: absolute; left: 57px; top: 945px; width: 816px; height: 1px; background: var(--line); }

  /* Footer */
  .footer-col { position: absolute; top: 973px; }
  .footer-title { font-family: "Roboto", Arial, sans-serif; font-weight: 500; font-size: 12px; color: var(--ink); margin-bottom: 9px; }
  .news-item { width: 185px; margin-bottom: 22px; }
  .news-date { font-size: 9px; color: var(--muted); }
  .news-text { font-size: 11px; line-height: 15px; color: var(--ink); }
  .quick-links li { list-style: none; font-size: 11px; line-height: 20px; color: var(--ink); }
  .contact-item { display: flex; gap: 10px; margin-bottom: 16px; font-size: 11px; line-height: 14px; color: var(--ink); }
  .contact-icon { width: 26px; height: 26px; border-radius: 50%; background: #f0f0f0; flex: none;
    display: flex; align-items: center; justify-content: center; }
  .contact-phone { font-size: 16px; line-height: 18px; }
  .newsletter p { width: 190px; font-size: 11px; line-height: 14.5px; color: var(--ink); margin-bottom: 10px; }
  .field { width: 188px; height: 25px; background: var(--field); border-radius: 2px; margin-bottom: 7px;
    font-size: 9px; color: var(--muted); padding: 7px 7px; }
  .subscribe { width: 188px; height: 25px; background: var(--dark); color: var(--white); border-radius: 2px;
    font-family: "Roboto", Arial, sans-serif; font-weight: 500; font-size: 11px; display: flex; align-items: center; justify-content: center; }

  .bottom-bar { position: absolute; left: 57px; top: 1166px; width: 816px; display: flex; justify-content: space-between; align-items: center; font-size: 10.5px; color: var(--muted); }
  .follow { display: flex; align-items: center; gap: 7px; color: var(--ink); }
  .social-dot { width: 20px; height: 20px; border-radius: 50%; background: var(--blue); }
</style>
</head>
<body>

<header class="site-header">
  <div class="brand"><span class="brand-dot"></span>THORNVALE</div>
  <div class="top-contact">
    <span>
      <svg width="10" height="10" viewBox="0 0 10 10"><path d="M2 1l2 2-1 1.3c.6 1.2 1.5 2.1 2.7 2.7L7 6l2 2-1.3 1.3C4.5 9 1 5.5.7 2.3z" fill="#1a8fd0"/></svg>
      (+44) 01632 960418
    </span>
    <span>
      <svg width="11" height="8" viewBox="0 0 11 8"><rect width="11" height="8" fill="#1a8fd0"/><path d="M0 0l5.5 4.5L11 0" stroke="#fff" fill="none"/></svg>
      info@thornvale.co.uk
    </span>
  </div>
  <nav class="main-nav">
    <a class="active">HOME</a><a>ABOUT US</a><a>WHAT WE DO</a><a>SERVICES</a><a>CONTACT</a>
  </nav>
  <div class="search-btn">
    <svg width="10" height="10" viewBox="0 0 10 10"><circle cx="4" cy="4" r="3" stroke="#fff" stroke-width="1.5" fill="none"/><path d="M6.3 6.3L9 9" stroke="#fff" stroke-width="1.5"/></svg>
  </div>
</header>

<section class="hero" role="img" aria-label="A lone oak tree in a green field under a grey cloudy sky">
  <div class="hero-arrow prev"><svg width="8" height="12" viewBox="0 0 8 12"><path d="M6 1L2 6l4 5" stroke="#fff" stroke-width="1.6" fill="none"/></svg></div>
  <div class="hero-arrow next"><svg width="8" height="12" viewBox="0 0 8 12"><path d="M2 1l4 5-4 5" stroke="#fff" stroke-width="1.6" fill="none"/></svg></div>
</section>

<section class="services">
  <div class="service-row">
    <article class="service">
      <div class="service-photo photo-cattle" role="img" aria-label="Herd of dairy cattle grazing on a green pasture"></div>
      <div class="service-body">
        <h3 class="service-title">CONSULTING</h3>
        <div class="service-rule rule-teal"></div>
        <p class="service-text">Providing management, technical and<br>networking (@Thornvale) services to...</p>
      </div>
    </article>
    <article class="service">
      <div class="service-photo photo-eggs" role="img" aria-label="Tray of white eggs with a single brown egg"></div>
      <div class="service-body">
        <h3 class="service-title">PRODUCTION</h3>
        <div class="service-rule rule-blue"></div>
        <p class="service-text">Establishing a “Farm of the Future”<br>production base to showcase regenerative...</p>
      </div>
    </article>
    <article class="service">
      <div class="service-photo photo-produce" role="img" aria-label="Crates of locally grown vegetables beside a chalkboard sign"></div>
      <div class="service-body">
        <h3 class="service-title">MARKETING</h3>
        <div class="service-rule rule-green"></div>
        <p class="service-text">Developing knowledge and markets in local<br>schools and communities via the “Our Local...</p>
      </div>
    </article>
  </div>
</section>

<h2 class="welcome-heading">
  <span class="welcome-script">Welcome to</span>
  <span class="welcome-name">THORNVALE</span>
</h2>
<p class="welcome-copy">Nam liber tempor cum soluta nobis eleifend option congue nihil imperdiet doming id quod mazim placerat facer<br>possim assum. Typi non habent claritatem insitam; est usus legentis in iis qui facit eorum claritatem. Claritas est<br>etiam processus dynamicus, qui sequitur mutationem consuetudium lectorum. Mirum est notare quam littera<br>gothica, quam nunc putamus parum claram, anteposuerit litterarum formas humanitatis per seacula quarta<br>decima et quinta decima. Eodem modo typi, qui nunc nobis videntur parum clari, fiant sollemnes in futurum.</p>
<a class="learn-more">Learn More</a>

<div class="divider"></div>

<footer>
  <div class="footer-col" style="left:57px">
    <h4 class="footer-title">RECENT NEWS</h4>
    <div class="news-item">
      <div class="news-date">10 MAR 2015</div>
      <div class="news-text">Mirum est notare quam littera gothi ca, quam nunc</div>
    </div>
    <div class="news-item">
      <div class="news-date">10 MAR 2015</div>
      <div class="news-text">Mirum est notare quam littera gothi ca, quam nunc</div>
    </div>
  </div>

  <div class="footer-col" style="left:266px">
    <h4 class="footer-title">QUICK LINKS</h4>
    <ul class="quick-links">
      <li>Home</li><li>About us</li><li>What we do</li><li>Services</li><li>Contact</li>
    </ul>
  </div>

  <div class="footer-col" style="left:454px">
    <h4 class="footer-title">GET IN TOUCH</h4>
    <div class="contact-item">
      <span class="contact-icon"><svg width="8" height="11" viewBox="0 0 8 11"><path d="M4 0a4 4 0 014 4c0 3-4 7-4 7S0 7 0 4a4 4 0 014-4z" fill="#444"/><circle cx="4" cy="4" r="1.3" fill="#f0f0f0"/></svg></span>
      <span>228. Lorem ipsum dolor amet<br>sit aremt sor- 859584</span>
    </div>
    <div class="contact-item">
      <span class="contact-icon"><svg width="11" height="11" viewBox="0 0 10 10"><path d="M2 1l2 2-1 1.3c.6 1.2 1.5 2.1 2.7 2.7L7 6l2 2-1.3 1.3C4.5 9 1 5.5.7 2.3z" fill="#444"/></svg></span>
      <span>Phone :<br><span class="contact-phone">(+44) 01632 960418</span></span>
    </div>
    <div class="contact-item">
      <span class="contact-icon"><svg width="11" height="9" viewBox="0 0 11 9"><path d="M0 3.5L5.5 0 11 3.5V9H0z" fill="#444"/><path d="M0 3.5l5.5 3.5L11 3.5" stroke="#f0f0f0" fill="none"/></svg></span>
      <span>Email :<br>info@thornvale.co.uk</span>
    </div>
  </div>

  <div class="footer-col newsletter" style="left:685px">
    <h4 class="footer-title">NEWSLETTER SIGNUP</h4>
    <p>Sign up to receive occasional e-mail updates about new features and special News from Thornvale.</p>
    <div class="field">Enter Your Name</div>
    <div class="field">Enter Your Email</div>
    <div class="subscribe">SUBSCRIBE</div>
  </div>

  <div class="bottom-bar">
    <span>© 2015Thornvale. All Rights Reserved &nbsp;•&nbsp; Terms and Conditions &nbsp;•&nbsp; Privacy Policy &nbsp;•&nbsp; Terms of Use</span>
    <span class="follow">Follow Us On <span class="social-dot"></span></span>
  </div>
</footer>

</body>
</html>
```